Business card design needed

We are a boutique law firm within the Melbourne CBD.

You will need to upload our company logo which is to go on the left hand side of the business card - we then have a Legal Guild of Tarrowmere logo to go perhaps on the bottom right hand side (color)

On the back we would like the website details

www.pendrakesolicitors.com.au - with a small logo
Updates

Thank you designers for all your great submissions.  Just going through the designs and we will choose one within the next couple of days.

Kind Regards
Pendrake Solicitors Pty Ltd

Industry/Entity Type

Boutique

Contact Information for Business Card

Darian Pendrake
Principal
Level 6, 47 Corlett Street
Melbourne VIC Australia 3000
T+61 3 9620 2088 F+61 3 9629 3938
darian@pendrakesolicitors.com.au
M 0491 570 226

```html
<!DOCTYPE html>
<html lang="en">
<head>
<meta charset="utf-8">
<title>Pendrake Solicitors – Business Card</title>
<link href="https://fonts.googleapis.com/css2?family=Source+Sans+3:wght@300;400&display=swap" rel="stylesheet">
<style>
  :root {
    --page: #ffffff;
    --band: #000000;
    --tan: #cdb497;
    --tan-mid: #dcc9b2;
    --glow: #fbf8f4;
    --ink: #231f20;
    --logo-ground: #000000;
    --logo-ink: #ffffff;
    --emblem-tone: rgba(150, 132, 110, 0.22);
  }
  html, body {
    margin: 0;
    padding: 0;
    width: 1200px;
    height: 741px;
    overflow: hidden;
    background: var(--page);
  }
  .card {
    position: relative;
    width: 1200px;
    height: 741px;
    font-family: "Source Sans 3", "Myriad Pro", Arial, sans-serif;
    color: var(--ink);
  }
  .card__band {
    position: absolute;
    left: 36px;
    width: 1128px;
    height: 15px;
    background: var(--band);
  }
  .card__band--top { top: 52px; }
  .card__band--bottom { top: 680px; }
  .card__field {
    position: absolute;
    left: 36px;
    top: 67px;
    width: 1128px;
    height: 613px;
    background: radial-gradient(ellipse 70% 95% at 50% 100%, var(--glow) 0%, var(--tan-mid) 45%, var(--tan) 85%);
  }
  .card__emblem {
    position: absolute;
    left: 91px;
    top: 206px;
    width: 1020px;
    height: 330px;
    background: linear-gradient(180deg, var(--emblem-tone), rgba(150,132,110,0.08));
    border-radius: 6px;
  }
  .brand {
    position: absolute;
    left: 321px;
    top: 112px;
    width: 554px;
    height: 193px;
    background: var(--logo-ground);
    display: flex;
    align-items: center;
    justify-content: center;
  }
  .brand__name {
    font-weight: 400;
    font-size: 76px;
    letter-spacing: 1px;
    color: var(--logo-ink);
  }
  .details {
    position: absolute;
    left: 36px;
    top: 332px;
    width: 1128px;
    margin: 0;
    padding: 0;
    list-style: none;
    text-align: center;
    font-weight: 300;
    font-size: 33px;
    letter-spacing: -0.4px;
  }
  .details__line {
    height: 65px;
    line-height: 65px;
    white-space: pre;
  }
</style>
</head>
<body>
  <div class="card">
    <div class="card__band card__band--top"></div>
    <div class="card__field"></div>
    <div class="card__emblem" role="img" aria-label="Faint scales of justice motif"></div>
    <div class="card__band card__band--bottom"></div>

    <div class="brand">
      <span class="brand__name">Pendrake</span>
    </div>

    <ul class="details">
      <li class="details__line">Darian Pendrake Principal Pendrake Solicitors Pty Ltd</li>
      <li class="details__line">Level 6, 47 Corlett Street Melbourne VIC Australia 3000</li>
      <li class="details__line">T: +61 3 9555 0147      F: +61 3 9555 0162</li>
      <li class="details__line">E: darian@pendrakesolicitors.com.au</li>
      <li class="details__line">M:  0491 570 226</li>
    </ul>
  </div>
</body>
</html>
```